Launching a new real estate agency in Monaco

Hello, I am opening a new real estate agency in Monaco. For the purpose of my activity, in order to be known quickly among a fierce competition I need an advertising campaign that will be broadcast in local magazines, newspapers, paper board, etc.

You will find example of pictures of Monaco on which I have the rights and my logo. You can always pick other images that I can buy if the price is reasonable for a commercial use (<200 $)

Please respect the color code.

I wish you good luck and look forward to give you my feedbacks

Reason: Only few projects posted were respecting the brief and of quality. Hoping to receive more in coming days

Target Market(s)

International high-end clientele of all ages, all genders.

Industry/Entity Type

Real Estate Agent

Font styles to use
Serif

Requirements
Must have
• 1/ My logo
• 2/ This message "Un nouveau regard sur l'immobilier" means in English a fresh look at real estate or new eyes on real-estate.
• 3/ My address: 14 rue des Ormeaux, Galerie Bellerive Nord, 98 000 Monaco
• 4/ Phone number: +377.93.48.25.07
• 5/ Website: www.corvano-immo.com.
• 6/ Format: Files should be easily adjustable but I'd like a vertical display to fit easily in Magazines, Poster and billboard. So please work in high resolution !
Nice to have
• Please think about your design in accordance with the message I want to display.
Should not have
• A simple poster with a picture of Monaco that does not take into consideration the message of the advertisement, "Un nouveau regard sur l'immobilier" which means in english, new eyes on real-estate or a new look at real-estate, or new vision at real-estate.

```html
<!DOCTYPE html>
<html lang="fr">
<head>
<meta charset="utf-8">
<title>Corvano Immo — Un nouveau regard sur l'immobilier</title>
<link rel="stylesheet" href="https://fonts.googleapis.com/css2?family=Cinzel:wght@400&family=Lato:wght@400&display=swap">
<style>
  :root {
    --shadow-deep: #2a1a1c;
    --warm-brown: #6b3a34;
    --skin-light: #d8c0b0;
    --skin-mid: #b58d80;
    --accent-red: #c8201c;
    --dusk-violet: #8a7aa6;
    --dusk-amber: #e6a35a;
    --rose-gold: #e2a893;
    --text-light: #f4eeea;
  }
  * { margin: 0; padding: 0; box-sizing: border-box; }
  html, body { width: 854px; height: 1200px; overflow: hidden; background: var(--shadow-deep); }
  .poster {
    position: relative;
    width: 854px;
    height: 1200px;
    overflow: hidden;
    font-family: "Lato", sans-serif;
    color: var(--text-light);
  }
  .poster__backdrop {
    position: absolute; inset: 0;
    background:
      radial-gradient(ellipse 260px 340px at 690px 930px, rgba(216,192,176,0.85), transparent 70%),
      radial-gradient(ellipse 300px 260px at 760px 170px, rgba(216,192,176,0.9), transparent 75%),
      radial-gradient(ellipse 420px 460px at 470px 590px, rgba(200,32,28,0.9), transparent 72%),
      linear-gradient(100deg, var(--shadow-deep) 0%, var(--warm-brown) 35%, var(--skin-mid) 70%, var(--skin-light) 100%);
  }
  .poster__view {
    position: absolute;
    left: 200px; top: 300px;
    width: 560px; height: 610px;
    border-radius: 48% 48% 50% 50% / 40% 40% 60% 60%;
    background:
      radial-gradient(ellipse 260px 220px at 65% 70%, rgba(230,163,90,0.85), transparent 75%),
      linear-gradient(180deg, #f0b27a 0%, var(--dusk-violet) 28%, #6d5a78 55%, #4a3a3e 100%);
  }
  .brand {
    position: absolute;
    left: 70px; top: 92px;
    display: flex; align-items: center; gap: 18px;
  }
  .brand__mark {
    width: 46px; height: 46px;
    border-radius: 50%;
    background: var(--rose-gold);
  }
  .brand__name {
    font-family: "Lato", sans-serif;
    font-size: 50px;
    letter-spacing: 4px;
    color: var(--rose-gold);
    text-transform: uppercase;
    line-height: 1;
  }
  .tagline {
    position: absolute;
    left: 67px; top: 356px;
    font-family: "Cinzel", serif;
    font-size: 36px;
    line-height: 44px;
    color: var(--text-light);
    text-shadow: 0 2px 4px rgba(0,0,0,0.6);
  }
  .tagline__line { display: block; }
  .tagline__line--indent { padding-left: 150px; }
  .contact {
    position: absolute;
    left: 67px; top: 1040px;
    font-size: 24px;
    line-height: 32px;
    color: var(--text-light);
  }
  .contact__sep { padding: 0 20px; }
</style>
</head>
<body>
  <main class="poster">
    <div class="poster__backdrop" role="img" aria-label="Photographie en gros plan d'une personne portant des lunettes rouges en forme de cœur"></div>
    <div class="poster__view" role="img" aria-label="Vue aérienne de Monaco au crépuscule, reflétée dans le verre des lunettes"></div>

    <header class="brand">
      <span class="brand__mark"></span>
      <span class="brand__name">Corvano Immo</span>
    </header>

    <h1 class="tagline">
      <span class="tagline__line">Un nouveau regard</span>
      <span class="tagline__line tagline__line--indent">sur l'immobilier</span>
    </h1>

    <address class="contact" style="font-style: normal;">
      <span>14 rue des Ormeaux, Galerie Bellerive Nord,</span><br>
      <span>98 000 Monaco</span><br>
      <span>+377.93.48.25.07</span><span class="contact__sep">I</span><span>www.corvano-immo.com</span>
    </address>
  </main>
</body>
</html>
```